Investment company needing business card

We are wanting a business card which looks sharp and easy on the eye. We are thinking of having a business card with the logo embossed on it, to really make it stand out. We will only have a small amount of information of the business card, person's name, position, email address and phone number

Contact Information for Business Card

Danielle Frost
Executive Assistant
+64 21 473 5162
danielf@harwickpartners.co.nz

Requirements
Must have
• Embossed logo
Should not have
• Not to be busy

```html
<!DOCTYPE html>
<html lang="en">
<head>
<meta charset="utf-8">
<title>Harwick Partners – Business Card</title>
<link href="https://fonts.googleapis.com/css2?family=Roboto:wght@400;700&display=swap" rel="stylesheet">
<style>
  :root {
    --backdrop: #3a3a3a;
    --card: #eeeeef;
    --brand-green: #25b86a;
    --ink-grey: #4d4d4f;
    --emboss-light: #fbfbfc;
    --emboss-shade: #cfcfd3;
  }
  * { margin: 0; padding: 0; box-sizing: border-box; }
  html, body {
    width: 1200px;
    height: 799px;
    overflow: hidden;
    background: var(--backdrop);
    font-family: "Roboto", sans-serif;
  }
  .canvas {
    position: relative;
    width: 1200px;
    height: 799px;
    display: flex;
    align-items: center;
    justify-content: center;
  }
  .business-card {
    position: relative;
    width: 340px;
    height: 570px;
    background: var(--card);
    box-shadow: 0 18px 40px rgba(0,0,0,0.45);
    text-align: center;
    overflow: hidden;
  }
  .brand {
    position: absolute;
    top: 54px;
    left: 0;
    right: 0;
    display: flex;
    align-items: center;
    justify-content: center;
    gap: 10px;
  }
  .brand-mark {
    width: 30px;
    height: 30px;
    background: var(--brand-green);
  }
  .brand-name {
    color: var(--ink-grey);
    font-weight: 700;
    font-size: 21px;
    letter-spacing: 1.5px;
    line-height: 1;
    text-transform: uppercase;
  }
  .person {
    position: absolute;
    top: 138px;
    left: 0;
    right: 0;
  }
  .person-name {
    color: var(--brand-green);
    font-weight: 700;
    font-size: 24px;
    letter-spacing: 0.3px;
    text-transform: uppercase;
    line-height: 1.05;
  }
  .person-role {
    color: var(--ink-grey);
    font-size: 14.5px;
    letter-spacing: 0.4px;
    text-transform: uppercase;
  }
  .divider {
    width: 22px;
    height: 2px;
    background: var(--ink-grey);
    margin: 16px auto 18px;
  }
  .contact {
    list-style: none;
    color: var(--ink-grey);
    font-size: 14px;
    line-height: 1.3;
  }
  .emboss {
    position: absolute;
    left: 88px;
    top: 300px;
    width: 236px;
    height: 236px;
  }
</style>
</head>
<body>
<main class="canvas">
  <article class="business-card">
    <header class="brand">
      <span class="brand-mark" aria-hidden="true"></span>
      <span class="brand-name">Harwick Partners</span>
    </header>

    <section class="person">
      <h1 class="person-name">Danielle Frost</h1>
      <p class="person-role">Executive Assistant</p>
      <div class="divider"></div>
      <ul class="contact">
        <li>+64 21 473 5162</li>
        <li>danielf@harwickpartners.co.nz</li>
        <li>www.harwickpartners.co.nz</li>
      </ul>
    </section>

    <svg class="emboss" viewBox="0 0 236 236" aria-hidden="true">
      <rect x="3" y="3" width="230" height="230" rx="34" fill="none"
            stroke="var(--emboss-light)" stroke-width="2.5"/>
      <rect x="5" y="5" width="230" height="230" rx="34" fill="none"
            stroke="var(--emboss-shade)" stroke-width="1.5"/>
    </svg>
  </article>
</main>
</body>
</html>
```